full stationary design for a modern sleek design company

we are a design company that does modern minimalistic interior design works as well as other design services for high end clients.
we need a full stationary design including and not limited to (double sided business card, letter head, envelopes, documents folder...etc) that reflects the modern style design we do.
sleek modern and minimalistic is the requirements.
Updates

please use the latest attached files as there was a slight modification on the logo Added Wednesday, March 1, 2017

minor update on the logo files in JPG and PSD has been updated kindly follow the new attachments. Added Thursday, March 2, 2017

Target Market(s)

modern minimalist clients

Industry/Entity Type

Design Agency

Requirements
Must have
• the logo
Nice to have
• i like the colors in the colored 3D logo attached
Should not have
• too many colors

```html
<!DOCTYPE html>
<html lang="en">
<head>
<meta charset="utf-8">
<title>Norrin Atelier – Business Card</title>
<link rel="stylesheet" href="https://fonts.googleapis.com/css2?family=Open+Sans:wght@400;600&display=swap">
<style>
  :root {
    --backdrop: #e8e5e1;
    --card-light: #ffffff;
    --card-dark: #323436;
    --accent: #f7941d;
    --ink: #3a3a3a;
    --ink-soft: #555555;
    --rule: #3a3a3a;
    --on-dark: #ffffff;
  }
  * { box-sizing: border-box; margin: 0; padding: 0; }
  html, body {
    width: 1200px;
    height: 987px;
    overflow: hidden;
    background: var(--backdrop);
    font-family: "Open Sans", Arial, sans-serif;
  }
  .canvas { position: relative; width: 1200px; height: 987px; }

  .card {
    position: absolute;
    left: 293px;
    width: 615px;
    height: 351px;
    box-shadow: 0 4px 10px rgba(0,0,0,0.18);
  }
  .card--front { top: 130px; background: var(--card-light); }
  .card--back  { top: 506px; background: var(--card-dark); }

  .brand {
    display: flex;
    align-items: center;
    gap: 12px;
    font-weight: 600;
    letter-spacing: 0.12em;
    text-transform: uppercase;
    white-space: nowrap;
  }
  .brand__square { width: 30px; height: 30px; background: var(--accent); flex: none; }
  .brand__name { font-size: 30px; line-height: 1; }

  .card--front .brand { position: absolute; right: 38px; top: 58px; }
  .card--front .brand__name { color: var(--ink); }

  .card--back .brand {
    position: absolute;
    left: 50%; top: 50%;
    transform: translate(-50%, -50%);
  }
  .card--back .brand__square { background: var(--on-dark); }
  .card--back .brand__name { color: var(--on-dark); font-size: 34px; }

  .person { position: absolute; left: 28px; top: 175px; right: 38px; }
  .person__name {
    color: var(--accent);
    font-weight: 600;
    font-size: 21px;
    line-height: 1.2;
    text-transform: uppercase;
  }
  .person__role-row { display: flex; align-items: center; }
  .person__role { color: var(--ink); font-size: 15px; line-height: 1.3; }
  .person__rule { flex: 1; height: 1px; background: var(--rule); margin-top: 3px; }

  .contact {
    position: absolute;
    left: 28px; top: 257px;
    list-style: none;
    color: var(--ink-soft);
    font-size: 15px;
    line-height: 23.5px;
  }
  .contact li { display: flex; align-items: center; gap: 8px; }
  .contact svg { width: 13px; height: 14px; fill: var(--accent); flex: none; }

  .address {
    position: absolute;
    right: 38px; top: 257px;
    text-align: right;
    font-style: normal;
    color: var(--ink-soft);
    font-size: 15px;
    line-height: 21.5px;
  }
</style>
</head>
<body>
<main class="canvas">
  <section class="card card--front" aria-label="Business card front">
    <div class="brand">
      <span class="brand__square"></span>
      <span class="brand__name">Norrin Atelier</span>
    </div>

    <div class="person">
      <h1 class="person__name">Elena Varga</h1>
      <div class="person__role-row">
        <span class="person__role">CEO&amp;Founder</span>
        <span class="person__rule"></span>
      </div>
    </div>

    <ul class="contact">
      <li>
        <svg viewBox="0 0 24 24" aria-hidden="true"><path d="M6.6 10.8a15.1 15.1 0 0 0 6.6 6.6l2.2-2.2c.3-.3.7-.4 1-.2 1.1.4 2.3.6 3.6.6.6 0 1 .4 1 1V20c0 .6-.4 1-1 1A17 17 0 0 1 3 4c0-.6.4-1 1-1h3.5c.6 0 1 .4 1 1 0 1.3.2 2.5.6 3.6.1.3 0 .7-.2 1z"/></svg>
        (555) 214 7730
      </li>
      <li>
        <svg viewBox="0 0 24 24" aria-hidden="true"><path d="M7 1h10a2 2 0 0 1 2 2v18a2 2 0 0 1-2 2H7a2 2 0 0 1-2-2V3a2 2 0 0 1 2-2zm0 3v14h10V4zm5 15.5a1.2 1.2 0 1 0 0 2.4 1.2 1.2 0 0 0 0-2.4z"/></svg>
        (555) 309 6481
      </li>
      <li>
        <svg viewBox="0 0 24 24" aria-hidden="true"><path d="M2 5h20v14H2zm2 2v.5l8 5 8-5V7zm0 2.8V17h16V9.8l-8 5z"/></svg>
        elena@norrinatelier.com
      </li>
    </ul>

    <address class="address">
      1420 Aspen Court<br>
      Juneau, Alaska 99801<br>
      www.norrinatelier.com
    </address>
  </section>

  <section class="card card--back" aria-label="Business card back">
    <div class="brand">
      <span class="brand__square"></span>
      <span class="brand__name">Norrin Atelier</span>
    </div>
  </section>
</main>
</body>
</html>
```